****Business Card Design for Quarrystone Development. Design based around attached logo/company name

I’m looking for business card design for my company Quarrystone Development Group,LLC. Design should be professional, sharp and minimal. Outside of the attached logos, greyscale colors for remainder of cards. My thoughts are two-sided card with attached logo on one side and my info on the other but open to one-sided as well with right design.
Target Market(s)
Real estate professionals including banks, private investors, property owners, developers, commercial tenants like Brewlantern, Grovika or Tanquist’s.
Industry/Entity Type
Commercial real estate development and investments.
Contact Information for Business Card
Name, title, email, phone #’s, web address and physical address
Font styles to use
Other font styles liked:
- Helvetica, Garamond, etc
Colors
Designer to choose only greyscale colors for use in the design.
Requirements
Must have
- Attached logo first or second options.
Nice to have
- Two sided card with logo on one side. Attached Logo/company name can be laid out any way that flows as long as it’s legible.name
Should not have
- No loud colors. ***Please do not include logo, I have removed the company design with a logo image.

```html
<!DOCTYPE html>
<html lang="en">
<head>
<meta charset="utf-8">
<title>Quarrystone Development Group, LLC — Business Card</title>
<link rel="stylesheet" href="https://fonts.googleapis.com/css2?family=Cinzel:wght@400;700&family=Arimo:wght@400&display=swap">
<style>
  :root {
    --page: #e9e8e5;
    --slate: #5a6476;
    --slate-light: #8c93a0;
    --stripe: #8a8a8c;
    --paper: #ffffff;
    --ink: #3f4756;
    --ink-soft: #6b7280;
    --rule: #a4a8b0;
    --on-slate: #e6e8ec;
  }
  * { box-sizing: border-box; margin: 0; padding: 0; }
  html, body { width: 1200px; height: 900px; overflow: hidden; }
  body {
    background: var(--page);
    display: flex;
    flex-direction: column;
    align-items: center;
    justify-content: center;
    gap: 40px;
    font-family: "Arimo", Helvetica, Arial, sans-serif;
  }
  .card {
    position: relative;
    width: 630px;
    height: 360px;
    box-shadow: 0 6px 18px rgba(0,0,0,0.18);
    overflow: hidden;
  }

  /* Front */
  .card--front {
    background: var(--slate);
    display: flex;
    align-items: center;
    justify-content: center;
    gap: 22px;
  }
  .brand-mark {
    width: 46px; height: 46px;
    border-radius: 50%;
    background: var(--slate-light);
  }
  .brand {
    font-family: "Cinzel", "Times New Roman", serif;
    font-weight: 400;
    color: var(--on-slate);
    line-height: 1;
  }
  .brand__name { display: block; font-size: 46px; letter-spacing: 2px; }
  .brand__sub { display: block; font-size: 13.5px; letter-spacing: 2.4px; margin-top: 8px; }

  /* Back */
  .card--back { background: var(--paper); }
  .card--back .brand { position: absolute; left: 40px; top: 48px; color: var(--ink-soft); }
  .card--back .brand__name { font-size: 34px; letter-spacing: 1.5px; }
  .card--back .brand__sub { font-size: 10px; letter-spacing: 1.8px; margin-top: 6px; }
  .card--back .brand-mark {
    position: absolute; right: 48px; top: 36px;
    width: 70px; height: 70px;
    background: var(--slate);
  }
  .person { position: absolute; left: 40px; top: 160px; }
  .person__name {
    font-family: "Cinzel", "Times New Roman", serif;
    font-weight: 700;
    font-size: 21px;
    letter-spacing: 1px;
    color: var(--ink);
  }
  .person__title { font-size: 13px; color: var(--ink-soft); margin-top: 4px; }
  .divider {
    position: absolute; left: 40px; right: 40px; top: 215px;
    height: 1px; background: var(--rule);
  }
  .contact {
    position: absolute; right: 40px; top: 118px;
    list-style: none;
    text-align: right;
    font-size: 13px;
    color: var(--ink-soft);
    line-height: 24px;
  }
  .contact li { display: flex; align-items: center; justify-content: flex-end; gap: 8px; }
  .contact svg { width: 11px; height: 11px; fill: none; stroke: var(--ink); stroke-width: 1.6; }
  .address {
    position: absolute; left: 40px; top: 242px;
    font-style: normal;
    font-size: 13px;
    line-height: 20px;
    color: var(--ink-soft);
  }
  .footer-band { position: absolute; left: 0; bottom: 0; width: 630px; height: 90px; }
</style>
</head>
<body>

  <section class="card card--front" aria-label="Card front">
    <span class="brand-mark" aria-hidden="true"></span>
    <div class="brand">
      <span class="brand__name">QUARRYSTONE</span>
      <span class="brand__sub">DEVELOPMENT GROUP, LLC</span>
    </div>
  </section>

  <section class="card card--back" aria-label="Card back">
    <div class="brand">
      <span class="brand__name">QUARRYSTONE</span>
      <span class="brand__sub">DEVELOPMENT GROUP, LLC</span>
    </div>
    <span class="brand-mark" aria-hidden="true"></span>

    <ul class="contact">
      <li>(503) 555-0148
        <svg viewBox="0 0 12 12"><path d="M2 1.5 L4 1.5 L5 4 L3.8 5 C4.5 6.5 5.5 7.5 7 8.2 L8 7 L10.5 8 L10.5 10 C6 10.5 1.5 6 2 1.5 Z"/></svg>
      </li>
      <li>info@quarrystonegroup.com
        <svg viewBox="0 0 12 12"><rect x="1" y="2.5" width="10" height="7"/><path d="M1 2.5 L6 6.5 L11 2.5"/></svg>
      </li>
      <li>www.quarrystonegroup.com
        <svg viewBox="0 0 12 12"><circle cx="6" cy="6" r="4.8"/><ellipse cx="6" cy="6" rx="2" ry="4.8"/><path d="M1.2 6 H10.8"/></svg>
      </li>
    </ul>

    <div class="person">
      <p class="person__name">DANIEL WHITCOMBE</p>
      <p class="person__title">Director</p>
    </div>

    <div class="divider"></div>

    <address class="address">1187 Larkspur Ridge<br>Corvallis, OR 97330</address>

    <svg class="footer-band" viewBox="0 0 630 90" aria-hidden="true">
      <path d="M0 90 L0 80 L395 80 C430 80 440 28 480 28 L630 28 L630 90 Z" fill="var(--slate)"/>
      <path d="M0 70 L385 70 C418 70 428 22 462 18" fill="none" stroke="var(--stripe)" stroke-width="4"/>
    </svg>
  </section>

</body>
</html>
```